DeskHarbor - Coworking website design

DeskHarbor is a new global coworking brand, growing fast and establishing stylish locations and communities that inspire innovation and collaboration all around the world.
The project includes a complete website design, focused on delivering the company’s values and messages, provide information to site visitors and to generate leads.

Please review the attached design brief, for more information.

Target Market(s)

Both men and women. Decision makers in:
Small & medium businesses in various fields, but mainly technology firms (Startups or established brands).
Global enterprises.
Dynamic “new generation” companies.
Press

Number of Pages Required

2 page

Requirements
Must have
• Project Scope & deliverables:
• Concept and design for :
• Home page
• Deliver the values mentioned above.
• Showcase the cities in which the company has locations in.
• Show customer testimonials.
• Provide an interface (form) for booking a tour and/or leaving contact details for more information (two alternatives)
• Coworking location page - Each location is in the coolest part of a different major city, and has its own address, set of amenities (kitchen, fast internet etc,), area information (public transportation accessibility, sites near by, bars and restaurants in walking distance) and pricing for private offices (based on number of people per office). Each location page must have an interface to book a location tour.
• Site Navigation (header & footer) - allow simple navigation between multiple city pages, location pages and homepage. Growth of up to 50 locations in 25 cities.
• The navigation should account for Navigation to additional pages (not commissioned in this project) such as:
• Locations
• Enterprise
• Special promotions
• Blog
• Contact us
• About us
• Note - the site should account for geolocation variable display, showing different content for different locations.
• Deliverables must include all editable graphic files (photoshop or similar), as follows:
• Home page - Desktop view (preferably both)
• Location page - Mobile web view (preferably both)
• Navigation - both options

```html
<!DOCTYPE html>
<html lang="en">
<head>
<meta charset="utf-8">
<title>DeskHarbor – Coworking spaces</title>
<link rel="stylesheet" href="https://fonts.googleapis.com/css2?family=Lora:ital,wght@0,400;0,700;1,400&display=swap">
<style>
:root{
  --navy:#1b3a78;
  --green:#2f8a1f;
  --ink:#222;
  --body:#555;
  --muted:#888;
  --line:#d6d6d6;
  --dark:#161616;
  --footer:#1d1d1d;
  --white:#fff;
}
*{box-sizing:border-box;margin:0;padding:0}
html,body{width:1200px;height:4245px;overflow:hidden}
body{position:relative;background:var(--white);font-family:"Lora",Georgia,serif;color:var(--ink)}
.abs{position:absolute}
/* header */
.site-header{left:0;top:0;width:1200px;height:95px;background:var(--white)}
.brand{left:100px;top:28px;font-size:34px;font-weight:700;color:var(--navy)}
.top-contact{top:16px;font-size:13px;color:var(--ink);display:flex;align-items:center;gap:10px}
.top-contact .dot{width:30px;height:30px;border-radius:50%;display:flex;align-items:center;justify-content:center}
.main-nav{top:64px;left:488px;display:flex;gap:33px;font-size:14px;font-weight:700;color:var(--ink)}
/* hero */
.hero{left:0;top:95px;width:1200px;height:510px;background:linear-gradient(120deg,#c9d6c4 0%,#e8ece4 30%,#9bb08e 55%,#e6e2d8 75%,#8f9a8a 100%)}
.hero-panel{left:311px;top:145px;width:594px;height:227px;background:rgba(20,20,20,.55);text-align:center;color:var(--white)}
.hero-panel h1{font-size:56px;font-weight:700;margin-top:22px}
.hero-panel p{font-size:22px;margin-top:6px}
.btn-outline{display:inline-block;margin-top:22px;border:2px solid var(--white);border-radius:22px;padding:8px 22px;font-size:13px;font-weight:700;color:var(--white)}
.dots{display:flex;gap:6px}
.dots i{width:10px;height:10px;border-radius:50%;background:var(--white);display:block}
.dots i.off{background:transparent;border:1.5px solid var(--white)}
/* finder */
.finder{left:100px;top:658px;width:440px}
.finder h2{font-size:30px;font-weight:700;letter-spacing:.5px}
.finder .lead{font-size:13px;color:var(--body);margin-top:10px;line-height:1.6}
.field-label{font-size:13px;font-weight:700;margin-top:20px}
.field{margin-top:10px;height:42px;border:1px solid var(--line);font-size:12px;color:var(--body);padding:12px 10px;position:relative}
.btn{display:inline-block;border-radius:22px;padding:11px 20px;font-size:13px;font-weight:700;color:var(--white)}
.btn-navy{background:var(--navy)}
.btn-green{background:var(--green)}
.photo{background:linear-gradient(135deg,#6d6a63,#b7aa92 50%,#3e3a35)}
.photo-frame{border:2px solid rgba(255,255,255,.85)}
.caption{font-size:13px;color:var(--ink)}
/* features */
.feature h3{font-size:22px;font-weight:700;color:var(--ink)}
.feature p{font-size:12.5px;line-height:2;color:var(--body);margin-top:22px}
.feature .btn{margin-top:24px}
/* testimonials */
.testimonials{left:0;top:2890px;width:1200px;height:440px;background:linear-gradient(180deg,#2a2520,#141210 60%,#2b241c)}
.testimonials h2{position:absolute;left:0;width:1200px;text-align:center;top:48px;font-size:30px;font-weight:700;color:var(--white)}
.quote{position:absolute;top:150px;width:470px;color:var(--white)}
.quote .avatar{width:72px;height:72px;border-radius:50%;border:3px solid var(--white);background:#8b8175}
.quote blockquote{font-style:italic;font-size:13px;line-height:1.7;margin-top:14px;color:#e6e6e6}
.quote .who{margin-top:18px;font-size:15px;font-weight:700}
.quote .city{font-size:13px;font-style:italic;color:#bbb;margin-top:4px;padding-left:14px}
/* contact */
.contact{left:100px;top:3400px;width:400px}
.contact h2{font-size:22px;font-weight:700}
.form-row{display:flex;align-items:center;margin-top:18px;font-size:12px;color:var(--body)}
.form-row span{width:52px}
.form-row div{flex:1;height:36px;border:1px solid #aaa}
.map{left:530px;top:3400px;width:570px;height:365px;border:1px solid #e3e3e3;background:linear-gradient(140deg,#2f9bd6,#56b6e8 45%,#1e84c2)}
/* footer */
.site-footer{left:0;top:3840px;width:1200px;height:405px;background:linear-gradient(180deg,#262626,var(--footer))}
.site-footer .brand-f{position:absolute;left:100px;top:65px;font-size:40px;font-weight:700;color:var(--white)}
.site-footer .about{position:absolute;left:100px;top:130px;width:300px;font-size:12px;line-height:1.8;color:#d0d0d0}
.fcol{position:absolute;top:75px;color:var(--white)}
.fcol h4{font-size:17px;font-weight:700;letter-spacing:.5px}
.fcol ul{list-style:none;margin-top:22px;font-size:12px;color:#ddd}
.fcol li{margin-bottom:14px;display:flex;gap:12px;align-items:flex-start}
.soc{width:26px;height:26px;border-radius:50%;display:inline-block;flex:none}
.copy{position:absolute;left:0;top:4180px;width:1200px;border-top:1px solid #444;text-align:center;font-size:12px;color:#ccc;padding-top:20px}
</style>
</head>
<body>

<header class="abs site-header">
  <div class="abs brand">DeskHarbor</div>
  <div class="abs top-contact" style="left:732px">
    <span class="dot" style="background:var(--navy)"><svg width="14" height="10" viewBox="0 0 14 10"><rect x="0.5" y="0.5" width="13" height="9" fill="none" stroke="#fff"/><path d="M1 1l6 5 6-5" fill="none" stroke="#fff"/></svg></span>
    info@deskharbor.com
  </div>
  <div class="abs top-contact" style="left:950px">
    <span class="dot" style="background:var(--green)"><svg width="14" height="14" viewBox="0 0 24 24"><path d="M6.6 10.8a15 15 0 006.6 6.6l2.2-2.2a1 1 0 011-.25 11.4 11.4 0 003.6.6 1 1 0 011 1V20a1 1 0 01-1 1A17 17 0 013 4a1 1 0 011-1h3.5a1 1 0 011 1 11.4 11.4 0 00.6 3.6 1 1 0 01-.25 1z" fill="#fff"/></svg></span>
    1-800-555-0142
  </div>
  <nav class="abs main-nav">
    <span>Locations</span><span>Enterprise</span><span>Special promotions</span><span>Blog</span><span>Contact us</span><span>About us</span>
  </nav>
</header>

<section class="abs hero" role="img" aria-label="Photo of people working together in a bright open coworking space">
  <div class="abs hero-panel">
    <h1>DeskHarbor</h1>
    <p>Sed ut perspiciatis unde omnis iste natus</p>
    <span class="btn-outline">LEARN MORE &gt;&gt;</span>
  </div>
  <div class="abs dots" style="left:568px;top:475px"><i class="off"></i><i></i><i></i><i></i></div>
</section>

<section class="abs finder">
  <h2>WHERE BUSINESSES THRIVE</h2>
  <p class="lead">Contrary to popular belief, Lorem Ipsum is not simply random text. It has roots in a piece of classical Latin literature</p>
  <div class="field-label">Where you want space?</div>
  <div class="field">Choose location
    <svg style="position:absolute;right:12px;top:17px" width="10" height="6" viewBox="0 0 10 6"><path d="M0 0h10L5 6z" fill="#555"/></svg>
  </div>
  <div class="field-label">How many employees</div>
  <div class="field">Employees to be work</div>
  <span class="btn btn-navy" style="margin-top:28px">STARTS NOW</span>
</section>
<div class="abs photo" style="left:595px;top:665px;width:505px;height:325px" role="img" aria-label="Photo of a team gathered around a table reviewing charts"></div>
<div class="abs caption" style="left:595px;top:1000px">Workspace,Location</div>
<svg class="abs" style="left:1063px;top:1004px" width="38" height="10" viewBox="0 0 38 10"><path d="M0 5h14M0 5l4-4M0 5l4 4M24 5h14M38 5l-4-4M38 5l-4 4" stroke="#333" stroke-width="1.5" fill="none"/></svg>

<!-- feature 1 -->
<div class="abs photo" style="left:100px;top:1078px;width:403px;height:307px;background:linear-gradient(135deg,#3a2a1e,#8a6a48 50%,#2a1f18)" role="img" aria-label="Photo of a warm wood-panelled lounge with people working">
  <div class="abs photo-frame" style="left:18px;top:18px;right:18px;bottom:18px"></div>
</div>
<article class="abs feature" style="left:553px;top:1075px;width:545px">
  <h3>Inspire collaboration &amp; Innovation</h3>
  <p>Lorem ipsum dolor sit amet, consectetur adipiscing elit, sed do eiusmod tempor incididunt ut labore et dolore magna aliqua. Ut enim ad minim veniam, quis nostrud exercitation ullamco laboris nisi ut aliquip ex ea commodo consequat. Duis aute irure dolor in reprehenderit in voluptate velit esse cillum dolore eu fugiat nulla pariatur. Excepteur sint occaecat cupidatat non proident, sunt in culpa qui officia deserunt mollit anim id est laborum.</p>
  <span class="btn btn-green">READ MORE &gt;&gt;</span>
</article>

<!-- feature 2 -->
<article class="abs feature" style="left:100px;top:1435px;width:545px">
  <h3>Idea sharing</h3>
  <p>Lorem ipsum dolor sit amet, consectetur adipiscing elit, sed do eiusmod tempor incididunt ut labore et dolore magna aliqua. Ut enim ad minim veniam, quis nostrud exercitation ullamco laboris nisi ut aliquip ex ea commodo consequat. Duis aute irure dolor in reprehenderit in voluptate velit esse cillum dolore eu fugiat nulla pariatur. Excepteur sint occaecat cupidatat non proident, sunt in culpa qui officia deserunt mollit anim id est laborum.</p>
  <span class="btn btn-navy">READ MORE &gt;&gt;</span>
</article>
<div class="abs photo" style="left:698px;top:1438px;width:402px;height:307px;background:linear-gradient(135deg,#d8d4cc,#9a8e80 50%,#5c544a)" role="img" aria-label="Photo of colleagues sharing ideas at a desk">
  <div class="abs photo-frame" style="left:18px;top:18px;right:18px;bottom:18px"></div>
</div>

<!-- feature 3 -->
<div class="abs photo" style="left:100px;top:1800px;width:403px;height:307px;background:linear-gradient(135deg,#cfc3b6,#8c7a68 50%,#4a3e34)" role="img" aria-label="Photo of a small group meeting around a laptop">
  <div class="abs photo-frame" style="left:18px;top:18px;right:18px;bottom:18px"></div>
</div>
<article class="abs feature" style="left:553px;top:1795px;width:545px">
  <h3>Be a part of an exclusive club</h3>
  <p>Lorem ipsum dolor sit amet, consectetur adipiscing elit, sed do eiusmod tempor incididunt ut labore et dolore magna aliqua. Ut enim ad minim veniam, quis nostrud exercitation ullamco laboris nisi ut aliquip ex ea commodo consequat. Duis aute irure dolor in reprehenderit in voluptate velit esse cillum dolore eu fugiat nulla pariatur. Excepteur sint occaecat cupidatat non proident, sunt in culpa qui officia deserunt mollit anim id est laborum.</p>
  <span class="btn btn-green">READ MORE &gt;&gt;</span>
</article>

<!-- feature 4 -->
<article class="abs feature" style="left:100px;top:2150px;width:545px">
  <h3>Realize your greatness</h3>
  <p>Lorem ipsum dolor sit amet, consectetur adipiscing elit, sed do eiusmod tempor incididunt ut labore et dolore magna aliqua. Ut enim ad minim veniam, quis nostrud exercitation ullamco laboris nisi ut aliquip ex ea commodo consequat. Duis aute irure dolor in reprehenderit in voluptate velit esse cillum dolore eu fugiat nulla pariatur. Excepteur sint occaecat cupidatat non proident, sunt in culpa qui officia deserunt mollit anim id est laborum.</p>
  <span class="btn btn-navy">READ MORE &gt;&gt;</span>
</article>
<div class="abs photo" style="left:698px;top:2152px;width:402px;height:308px;background:linear-gradient(135deg,#e4e2de,#a9a49c 50%,#6c665e)" role="img" aria-label="Photo of a focused professional working at a computer">
  <div class="abs photo-frame" style="left:18px;top:18px;right:18px;bottom:18px"></div>
</div>

<!-- feature 5 -->
<div class="abs photo" style="left:100px;top:2508px;width:403px;height:310px;background:linear-gradient(135deg,#6a6a66,#b8b4ac 45%,#c0392b 90%)" role="img" aria-label="Photo of two people relaxing in white lounge chairs">
  <div class="abs photo-frame" style="left:18px;top:18px;right:18px;bottom:18px"></div>
</div>
<article class="abs feature" style="left:553px;top:2505px;width:545px">
  <h3>Style and design awareness</h3>
  <p>Lorem ipsum dolor sit amet, consectetur adipiscing elit, sed do eiusmod tempor incididunt ut labore et dolore magna aliqua. Ut enim ad minim veniam, quis nostrud exercitation ullamco laboris nisi ut aliquip ex ea commodo consequat. Duis aute irure dolor in reprehenderit in voluptate velit esse cillum dolore eu fugiat nulla pariatur. Excepteur sint occaecat cupidatat non proident, sunt in culpa qui officia deserunt mollit anim id est laborum.</p>
  <span class="btn btn-green">READ MORE &gt;&gt;</span>
</article>

<!-- testimonials -->
<section class="abs testimonials" role="img" aria-label="Dark photo of a coworking hall behind customer testimonials">
  <h2>TESTIMONIALS</h2>
  <div class="quote" style="left:100px">
    <div class="avatar" role="img" aria-label="Customer portrait"></div>
    <blockquote>“At vero eos et accusamus et iusto odio dignissimos ducimus qui blanditiis praesentium voluptatum deleniti atque corrupti quos dolores et quas molestias excepturi sint occaecati cupiditate non provident, similique sunt in culpa”</blockquote>
    <div class="who">– Person Name</div>
    <div class="city">City Name</div>
  </div>
  <div class="quote" style="left:590px">
    <div class="avatar" role="img" aria-label="Customer portrait" style="background:#9a9088"></div>
    <blockquote>“ Quisque in laoreet ipsum, vel dapibus est. Nulla pellentesque faucibus vulputate. Integer consequat leo eget dui interdum vulputate. Sed commodo sagittis lorem nec rutrum. Nam at tortor imperdiet, integer sollicitudin neque quis ullamcorper fermentum”</blockquote>
    <div class="who">– Person Name</div>
    <div class="city">City Name</div>
  </div>
  <div class="abs dots" style="left:1040px;top:370px"><i class="off"></i><i></i><i></i><i></i></div>
</section>

<!-- contact -->
<section class="abs contact">
  <h2>Contact Details</h2>
  <div class="form-row"><span>Name</span><div></div></div>
  <div class="form-row"><span>Email</span><div></div></div>
  <div class="form-row"><span>Phone</span><div></div></div>
  <div style="font-size:12px;color:var(--body);margin-top:18px">What you want to know</div>
  <div style="margin-top:12px;margin-left:52px;height:58px;border:1px solid #aaa"></div>
  <span class="btn btn-green" style="margin-top:28px">CONTACT NOW</span>
</section>
<div class="abs map" role="img" aria-label="World map marking the cities with DeskHarbor locations"></div>

<!-- footer -->
<footer class="abs site-footer">
  <div class="brand-f">DeskHarbor</div>
  <p class="about">Lorem ipsum dolor sit amet, consectetur adipiscing elit, sed do eiusmod tempor incididunt ut labore et dolore magna aliqua. Ut enim ad minim veniam, reprehenderit in voluptate velit esse cillum</p>
  <div class="fcol" style="left:460px">
    <h4>CONTACT US</h4>
    <ul>
      <li><svg width="12" height="16" viewBox="0 0 12 16"><path d="M6 0a6 6 0 00-6 6c0 4.5 6 10 6 10s6-5.5 6-10a6 6 0 00-6-6zm0 8.2A2.2 2.2 0 116 3.8a2.2 2.2 0 010 4.4z" fill="#fff"/></svg><span>Harbor Lane,<br>DeskHarbor Building, 1st Floor</span></li>
      <li><svg width="12" height="12" viewBox="0 0 24 24"><path d="M6.6 10.8a15 15 0 006.6 6.6l2.2-2.2a1 1 0 011-.25 11.4 11.4 0 003.6.6 1 1 0 011 1V20a1 1 0 01-1 1A17 17 0 013 4a1 1 0 011-1h3.5a1 1 0 011 1 11.4 11.4 0 00.6 3.6 1 1 0 01-.25 1z" fill="#fff"/></svg><span>1-800-555-0199</span></li>
      <li><svg width="13" height="10" viewBox="0 0 14 10"><rect x="0.5" y="0.5" width="13" height="9" fill="none" stroke="#fff"/><path d="M1 1l6 5 6-5" fill="none" stroke="#fff"/></svg><span>support@deskharbor.co</span></li>
    </ul>
  </div>
  <div class="fcol" style="left:740px">
    <h4>QUICK LINKS</h4>
    <ul>
      <li>›&nbsp; Locations</li><li>›&nbsp; Enterprise</li><li>›&nbsp; Special promotions</li><li>›&nbsp; Blog</li><li>›&nbsp; Contact us</li><li>›&nbsp; About us</li>
    </ul>
  </div>
  <div class="fcol" style="left:960px">
    <h4>SOCIAL MEDIA</h4>
    <ul>
      <li style="align-items:center"><span class="soc" style="background:#3b5998"></span>Pagebook</li>
      <li style="align-items:center"><span class="soc" style="background:#1da1f2"></span>Chirper</li>
      <li style="align-items:center"><span class="soc" style="background:#e0572a"></span>CirclePlus</li>
      <li style="align-items:center"><span class="soc" style="background:#cc1f1f"></span>Vidstream</li>
    </ul>
  </div>
</footer>
<div class="copy">Copyright ©2017 DeskHarbor. All Rights Reserved.</div>

</body>
</html>
```